Harrow Tavern & Grille Menu Makeover

I am looking for a professional look to update our current menu. We are an independently owned sports bar and grill. Up to this point, I have done all of my own graphic designing. I am looking for something classy/family oriented. We are a very family friendly sports bar that offers a wide variety of menu options. Our website is www.harrowtavernco.example. This may help you get more of a feel for what type of place we are and what we offer. Our menu is listed on the website. My current menu is 8.5x14 inserts that feature a cover page, 4 inside pages and a back page. I would like something a little more condensed than this. Possibly a large tri-fold menu? I am open to all new ideas. I do have some pictures on my menu now, and would like to continue using a few pictures to feature some of my items. I would like something that is in a format that gives me the option to change items and prices on my own in the future. I would also like it to feature, or inform my patrons about our technology that we offer. We offer online ordering and we are a "verified venue" with Brewvoke.( a social site for craft beer lovers).

Industry/Entity Type

Sports Bar

Requirements
Nice to have
• Nice to have some pictures, but does not have to. We do feature 9 different beers on tap. A lot of them are local craft beers from the state of Kansas. Not sure if that is something we can feature, but it is a nice talking point. All of our tables and bar are hand built. With a rich mahogany finish on all of our woodwork, some type of "woodgrain" look into the menu would be nice.

```html
<!DOCTYPE html>
<html lang="en">
<head>
<meta charset="utf-8">
<title>Harrow Tavern &amp; Grille – Appetizers</title>
<link rel="stylesheet" href="https://fonts.googleapis.com/css2?family=Cinzel:wght@400;700&family=Oswald:wght@300;400&family=Michroma&display=swap">
<style>
  :root {
    --wood-dark: #4a1d0b;
    --wood-mid: #7a3517;
    --wood-light: #9a4f25;
    --ink: #1f140c;
    --ink-soft: #3a2918;
    --white: #f4ece0;
    --photo-green: #6f8a3a;
    --photo-gold: #c9a04a;
  }
  * { margin: 0; padding: 0; box-sizing: border-box; }
  html, body { width: 850px; height: 1200px; overflow: hidden; }
  body {
    position: relative;
    background:
      linear-gradient(90deg, rgba(0,0,0,.28) 0%, rgba(0,0,0,0) 18%, rgba(255,255,255,.05) 50%, rgba(0,0,0,0) 82%, rgba(0,0,0,.3) 100%),
      linear-gradient(180deg, var(--wood-light) 0%, var(--wood-mid) 45%, var(--wood-dark) 100%);
    color: var(--ink);
  }
  .masthead { position: absolute; left: 0; top: 0; width: 850px; height: 160px; }
  .masthead__rule { position: absolute; height: 2px; background: var(--ink); }
  .masthead__rule::before, .masthead__rule::after {
    content: ""; position: absolute; top: -2px; width: 6px; height: 6px; border-radius: 50%; background: var(--ink);
  }
  .masthead__rule::before { left: -3px; }
  .masthead__rule::after { right: -3px; }
  .masthead__rule--top { left: 257px; top: 56px; width: 336px; }
  .masthead__rule--bottom { left: 319px; top: 143px; width: 214px; }
  .masthead__name {
    position: absolute; left: 0; top: 62px; width: 850px; text-align: center;
    font-family: "Cinzel", serif; font-weight: 700; font-size: 40px; letter-spacing: 12px; color: var(--ink);
  }
  .masthead__tagline {
    position: absolute; left: 0; top: 110px; width: 850px; text-align: center;
    font-family: "Cinzel", serif; font-weight: 700; font-size: 17px; letter-spacing: 1px; color: var(--ink);
  }
  .parchment { position: absolute; left: 0; top: 0; }
  .feature-photo { position: absolute; border-radius: 50%; border: 2px solid #1a1008; }
  .feature-photo--rattlesnake {
    left: 590px; top: 368px; width: 155px; height: 155px;
    background: radial-gradient(circle at 50% 45%, #e9e2cf 0 12%, var(--photo-gold) 30%, var(--photo-green) 62%, #141008 100%);
  }
  .feature-photo--onion {
    left: 77px; top: 776px; width: 176px; height: 176px;
    background: radial-gradient(circle at 45% 45%, #d9a457 0 30%, #b7792e 55%, #f1efea 80%);
  }
  .section-title {
    position: absolute; left: 0; top: 246px; width: 850px; text-align: center;
    font-family: "Cinzel", serif; font-weight: 700; font-size: 35px; color: var(--ink);
  }
  .menu-item { position: absolute; left: 255px; width: 340px; text-align: center; color: var(--ink-soft); }
  .menu-item__name {
    font-family: "Oswald", sans-serif; font-weight: 300; font-size: 15px; line-height: 16px; color: var(--ink); text-transform: uppercase;
  }
  .menu-item__desc {
    font-family: "Oswald", sans-serif; font-weight: 300; font-size: 8.8px; line-height: 12px; text-transform: uppercase; padding: 0 8px;
  }
  .menu-item__price {
    font-family: "Oswald", sans-serif; font-weight: 400; font-size: 7.5px; line-height: 8px; letter-spacing: .5px;
  }
  .contact-row {
    position: absolute; left: 0; top: 1045px; width: 850px; height: 20px;
    display: flex; justify-content: center; align-items: center;
  }
  .contact-row__item { display: flex; align-items: center; gap: 12px; margin: 0 14px; }
  .contact-row__mark { display: block; width: 18px; height: 18px; background: var(--ink); border-radius: 2px; flex: none; }
  .contact-row__text {
    font-family: "Michroma", sans-serif; font-size: 7px; letter-spacing: .4px; color: var(--ink); text-transform: uppercase; white-space: nowrap;
  }
  .portion-note {
    position: absolute; left: 0; top: 1152px; width: 850px; text-align: center;
    font-family: "Michroma", sans-serif; font-size: 6.4px; letter-spacing: .3px; color: var(--white); text-transform: uppercase;
  }
</style>
</head>
<body>
  <header class="masthead">
    <div class="masthead__rule masthead__rule--top"></div>
    <h1 class="masthead__name">HARROW</h1>
    <p class="masthead__tagline">Tavern &amp; Grille</p>
    <div class="masthead__rule masthead__rule--bottom"></div>
  </header>

  <svg class="parchment" width="850" height="1200" viewBox="0 0 850 1200" aria-hidden="true">
    <defs>
      <radialGradient id="parchmentFill" cx="50%" cy="48%" r="65%">
        <stop offset="0%" stop-color="#dcc49a"/>
        <stop offset="65%" stop-color="#c9a972"/>
        <stop offset="100%" stop-color="#94693a"/>
      </radialGradient>
    </defs>
    <path fill="url(#parchmentFill)" stroke="#6b4a24" stroke-width="1"
      d="M78 198 L120 190 L128 180 L210 186 L262 194 L300 186 L360 196 L420 190 L470 196 L520 188 L580 200 L640 194 L700 206 L740 190 L760 200 L790 214 L798 260 L790 300 L800 360 L794 420 L802 470 L796 540 L804 600 L796 660 L800 720 L792 780 L800 840 L794 900 L802 960 L794 1020 L788 1070 L792 1100 L760 1108 L700 1112 L660 1104 L610 1114 L560 1106 L500 1116 L440 1104 L380 1112 L320 1106 L260 1116 L200 1106 L150 1112 L100 1100 L60 1108 L42 1090 L48 1040 L38 990 L44 930 L34 870 L42 810 L36 760 L44 700 L36 640 L42 580 L34 520 L42 460 L36 400 L44 340 L36 280 L48 230 Z"/>
  </svg>

  <div class="feature-photo feature-photo--rattlesnake" role="img" aria-label="Photo of rattlesnake eggs around a cup of ranch dressing on lettuce"></div>
  <div class="feature-photo feature-photo--onion" role="img" aria-label="Photo of a golden deep-fried blooming onion"></div>

  <h2 class="section-title">APPETIZERS</h2>

  <main>
    <div class="menu-item" style="top:296px">
      <h3 class="menu-item__name">Slider Burgers</h3>
      <p class="menu-item__desc">Six juicy bite sized burgers topped with American cheese and served with pickle slices.</p>
      <p class="menu-item__price">8.99</p>
    </div>
    <div class="menu-item" style="top:352px">
      <h3 class="menu-item__name">Loaded Potato Skins</h3>
      <p class="menu-item__desc">Six crispy skins loaded with jack, cheddar and mozzarella cheese, then topped with smoked bacon and green onions. Served with sour cream.</p>
      <p class="menu-item__price">8.99</p>
    </div>
    <div class="menu-item" style="top:408px">
      <h3 class="menu-item__name">Rattlesnake Eggs</h3>
      <p class="menu-item__desc">A spicy combo of pepper jack cheese and jalapeños, battered and fried.</p>
      <p class="menu-item__price">7.99</p>
    </div>
    <div class="menu-item" style="top:452px">
      <h3 class="menu-item__name">Mozzarella Cheese Sticks</h3>
      <p class="menu-item__desc">Classic battered mozzarella cheese sticks served with ranch dressing.</p>
      <p class="menu-item__price">7.99</p>
    </div>
    <div class="menu-item" style="top:496px">
      <h3 class="menu-item__name">Grand Slam French Fries</h3>
      <p class="menu-item__desc">French fries loaded with jack, cheddar, mozzarella, bacon, jalapeños and green onions! Served with ranch dressing.</p>
      <p class="menu-item__price">7.99</p>
    </div>
    <div class="menu-item" style="top:552px">
      <h3 class="menu-item__name">Bang Bang Shrimp</h3>
      <p class="menu-item__desc">Lightly breaded and fried shrimp coated with a spicy Thai sauce, topped with parmesan cheese and diced tomatoes. Served over a bed of romaine lettuce.</p>
      <p class="menu-item__price">7.99</p>
    </div>
    <div class="menu-item" style="top:608px">
      <h3 class="menu-item__name">Ballpark Pretzel Basket</h3>
      <p class="menu-item__desc">Buttered and salted pretzels served with nacho cheese sauce.</p>
      <p class="menu-item__price">7.99</p>
    </div>
    <div class="menu-item" style="top:652px">
      <h3 class="menu-item__name">Spicy Southwest<br>Chicken Eggrolls</h3>
      <p class="menu-item__desc">Stuffed with black beans, corn and chicken.<br>Served with southwest ranch.</p>
      <p class="menu-item__price">9.99</p>
    </div>
    <div class="menu-item" style="top:724px">
      <h3 class="menu-item__name">Blooming Onion</h3>
      <p class="menu-item__desc">This fan favorite is classically carved and deep fried to perfection. Served with Harrow signature dipping sauce.</p>
      <p class="menu-item__price">7.99</p>
    </div>
    <div class="menu-item" style="top:780px">
      <h3 class="menu-item__name">Chicken Quesadilla</h3>
      <p class="menu-item__desc">A 12 inch flour tortilla stuffed with grilled chicken and jack and cheddar cheese. Served with salsa.</p>
      <p class="menu-item__price">8.99</p>
    </div>
    <div class="menu-item" style="top:836px">
      <h3 class="menu-item__name">Hollis's Boneless Buffalo Wings</h3>
      <p class="menu-item__desc">A full pound of spicy, boneless buffalo wings. Served with ranch dressing or Hollis's Gold Label sauce.</p>
      <p class="menu-item__price">7.99</p>
    </div>
    <div class="menu-item" style="top:892px">
      <h3 class="menu-item__name">Harrow Loaded Nachos</h3>
      <p class="menu-item__desc">Tri-colored tortilla chips smothered with creamy monterey jack cheese, choice of beef or chicken, and topped with grilled peppers and onions, jalapeños and diced tomatoes. Served with sour cream and salsa.</p>
      <p class="menu-item__price">9.99</p>
    </div>
    <div class="menu-item" style="top:960px">
      <h3 class="menu-item__name">Garlic Bread Basket</h3>
      <p class="menu-item__desc">Tri-colored tortilla chips smothered with creamy monterey jack cheese, choice of beef or chicken, and topped with grilled peppers and onions, jalapeños and diced tomatoes. Served with sour cream and salsa.</p>
      <p class="menu-item__price">9.99</p>
    </div>
  </main>

  <footer>
    <div class="contact-row">
      <div class="contact-row__item">
        <span class="contact-row__mark"></span>
        <span class="contact-row__text">harrowtavernandgrille</span>
      </div>
      <div class="contact-row__item">
        <span class="contact-row__mark"></span>
        <span class="contact-row__text">harrowtavernco.example</span>
      </div>
      <div class="contact-row__item">
        <span class="contact-row__text">Brewvoke</span>
      </div>
    </div>
    <p class="portion-note">When splitting a large portion, you will be charged the price of a small portion if a small portion is offered</p>
  </footer>
</body>
</html>
```